Harwick Moss Fine Art gallery website - Modern british art for sale

We need a website design that is both current and high end. Our products are expensive and this should be reflected in the look of the website. We would like the logo we had designed last year to be clearly seen in the design. We want sleek, simple, and easy to navigate. Nothing too colourful as the colours of the art should always take precedence.

Target Market(s)

The average price of one our products starts at £250 and can go up to £10,000 we are an entry level gallery.

Industry/Entity Type

Art Gallery

Number of Pages Required

5+ page

Font styles to use
Sans Serif

Colors
000000
ffffff
faa54b
abd037
886aae
b868aa

Requirements
Must have
• Attractive front page. Linked to our Social feed.
• 4 links from front page - New Releases, about us, Artists, contact us
• Social media links - Social link one, Social, Social link three, Social link four.
• Each artist must have their own page, each page must have a biography link to another page.
Nice to have
• Utilise our new logo design. I would like the Social feed to link to the front page in a small way so you can see what's being said on Social by the company. For future proofing maybe have a locations function on the front page which can be adroit down menu showing where our other galleries are.

```html
<!DOCTYPE html>
<html lang="en">
<head>
<meta charset="utf-8">
<title>Harwick Moss Fine Art</title>
<link rel="stylesheet" href="https://fonts.googleapis.com/css2?family=Cinzel:wght@400;700&family=Lato:wght@400;700&display=swap">
<style>
:root{
  --ink:#111;
  --night:#1b1b1d;
  --night-2:#2c2c2f;
  --gold:#fcd56a;
  --gold-2:#f7c24c;
  --orange:#faa54b;
  --green:#abd037;
  --violet:#886aae;
  --orchid:#b868aa;
  --paper:#ffffff;
  --mist:#f4f4f4;
  --rule:#dcdcdc;
  --link:#1a9ad6;
  --text:#222;
}
*{box-sizing:border-box;margin:0;padding:0}
html,body{width:750px;height:1200px;overflow:hidden}
body{position:relative;background:var(--paper);font-family:'Lato',sans-serif;color:var(--text)}
.abs{position:absolute}

.site-header{left:0;top:0;width:750px;height:87px;background:radial-gradient(ellipse at 50% 0%,var(--night-2),var(--night) 70%)}
.brand{left:0;width:750px;top:46px;text-align:center;font-family:'Cinzel',serif;font-size:22px;line-height:26px;color:#e9e9e9;letter-spacing:1px}
.brand-dot{display:inline-block;width:8px;height:8px;border-radius:50%;background:var(--gold-2);margin-right:8px;vertical-align:middle}
.main-nav{left:0;top:87px;width:750px;height:27px;background:linear-gradient(var(--gold),var(--gold-2));display:flex;justify-content:center;align-items:center}
.nav-link{font-family:'Cinzel',serif;font-size:11px;font-weight:700;color:var(--ink);padding:0 18px;border-left:1px solid rgba(0,0,0,.15)}
.nav-link:first-child{border-left:0}

.hero-art{left:57px;top:138px;width:316px;height:368px;background:linear-gradient(135deg,#e8e6ef,#f7f7f5 60%,#e6e5ea)}
.hero-panel{left:373px;top:138px;width:320px;height:368px;background:var(--orchid);color:#fff}
.hero-title{left:26px;top:185px;font-family:'Cinzel',serif;font-weight:400;font-size:19px;letter-spacing:.5px;white-space:nowrap}
.hero-text{left:26px;top:216px;width:272px;font-size:8.5px;line-height:12px}
.hero-rule{left:26px;top:283px;width:270px;height:1px;background:rgba(255,255,255,.35)}
.thumb{top:297px;width:66px;height:59px;border:2px solid #fff}
.thumb.active{border-color:#222}
.t1{left:26px;background:linear-gradient(#eee,#c8c8c8 60%,#e2572a)}
.t2{left:95px;background:linear-gradient(135deg,#e9ecef,#b8c4cc 60%,#e9574a)}
.t3{left:164px;background:linear-gradient(135deg,#f2f2f2,#9a9a9a)}
.t4{left:233px;background:linear-gradient(135deg,#fafafa,#cfcfcf)}
.hero-toggle{left:361px;top:454px;width:12px;height:24px;background:var(--orchid)}

.showcase{left:0;top:528px;width:750px;height:262px;background:var(--mist)}
.card{top:26px;height:204px}
.card-a{left:56px;width:317px;background:linear-gradient(90deg,#2e3a7e 0%,#2e3a7e 30%,#c8cfe0 40%,#f2bb2c 60%,#f2c02f 100%)}
.card-b{left:376px;width:317px;background:linear-gradient(135deg,#e9643a,#b48ad0 35%,#e4c46a 65%,#ef6a3e)}
.card-caption{left:0;bottom:0;width:100%;height:55px;background:rgba(255,255,255,.82);text-align:center}
.card-title{padding-top:8px;font-family:'Cinzel',serif;font-weight:700;font-size:17px;color:var(--ink)}
.card-date{font-size:10px;margin-top:2px}
.arrow{top:108px}

.section-head{font-family:'Cinzel',serif;font-weight:400;font-size:17px;color:var(--ink);border-bottom:1px solid var(--rule);padding-bottom:5px;display:flex;align-items:center;white-space:nowrap}
.head-mark{width:8px;height:8px;background:var(--ink);margin-right:10px}
.about{left:58px;top:820px;width:314px}
.about-text{margin-top:12px;font-size:8.5px;line-height:14px;text-align:justify}
.tweets{left:400px;top:820px;width:292px}
.see-all{margin-left:auto;font-family:'Lato',sans-serif;font-size:7.5px;color:var(--link)}
.tweet{display:flex;gap:10px;padding:10px 0 8px;border-bottom:1px solid #eee;font-size:7.5px;line-height:13px}
.tweet:last-child{border-bottom:0}
.tweet-badge{flex:none;width:33px;height:33px;border-radius:50%;border:2px solid var(--link);margin-top:2px}
.tweet b{font-weight:400;color:var(--link)}

.newsletter{left:0;top:980px;width:750px;height:76px;background:var(--mist)}
.news-icon{left:119px;top:30px;width:34px;height:34px;border-radius:50%;background:var(--orange)}
.news-title{left:165px;top:34px;font-family:'Cinzel',serif;font-size:13px;color:#333}
.news-sub{left:165px;top:51px;font-size:8px;color:#555}
.news-input{left:323px;top:34px;width:210px;height:28px;border:1px solid #ccc;background:#fff;font-size:8.5px;padding:9px 8px;color:#222}
.news-button{left:533px;top:34px;width:97px;height:28px;background:var(--orange);color:#fff;font-family:'Cinzel',serif;font-size:11px;text-align:center;line-height:28px;letter-spacing:.5px}

.site-footer{left:0;top:1056px;width:750px;height:144px;background:radial-gradient(ellipse at 50% 40%,var(--night-2),var(--night) 70%)}
.social{top:58px;width:19px;height:19px;background:#fff}
.footer-nav{left:0;top:93px;width:750px;display:flex;justify-content:center}
.footer-link{font-family:'Cinzel',serif;font-size:9px;color:#cfcfcf;padding:0 19px;border-left:1px solid #555}
.footer-link:first-child{border-left:0}
.copyright{left:0;top:113px;width:750px;text-align:center;font-size:7.5px;color:#bbb}
.stripe{left:0;top:1197px;width:750px;height:3px;display:flex}
.stripe i{flex:1}
</style>
</head>
<body>

<header class="abs site-header">
  <div class="abs brand"><span class="brand-dot"></span>Harwick Moss Fine Art</div>
</header>
<nav class="abs main-nav">
  <span class="nav-link">New Releases</span>
  <span class="nav-link">About Us</span>
  <span class="nav-link">Artists</span>
  <span class="nav-link">Location</span>
</nav>

<section>
  <div class="abs hero-art" role="img" aria-label="Pencil drawing of abstract seated figures on a pale ground"></div>
  <div class="abs hero-panel">
    <h1 class="abs hero-title">Hallam Sitting Figures</h1>
    <p class="abs hero-text">Lorem ipsum dolor sit amet, consectetuer adipiscing elit, sed diam sit nonummy nibh euismod tincidunt ut laoreet dolore magna aliquam erat volutpat. Ut wisi enim ad minim veniam, quis nostrud exerci tation almet ullamcorper suscipit lobortis nisl ut aliquip ex.</p>
    <div class="abs hero-rule"></div>
    <div class="abs thumb t1" role="img" aria-label="Artwork thumbnail: tower print"></div>
    <div class="abs thumb t2" role="img" aria-label="Artwork thumbnail: abstract line print"></div>
    <div class="abs thumb t3" role="img" aria-label="Artwork thumbnail: ink drawing"></div>
    <div class="abs thumb t4 active" role="img" aria-label="Artwork thumbnail: seated figures"></div>
  </div>
  <div class="abs hero-toggle">
    <svg width="12" height="24" viewBox="0 0 12 24"><path d="M4.5 9.5 2.5 12l2 2.5M7.5 9.5l2 2.5-2 2.5" fill="none" stroke="#fff" stroke-width="1.3"/></svg>
  </div>
</section>

<section class="abs showcase">
  <svg class="abs arrow" style="left:14px" width="20" height="40" viewBox="0 0 20 40"><path d="M18 2 3 20l15 18" fill="none" stroke="#999" stroke-width="2"/></svg>
  <div class="abs card card-a" role="img" aria-label="Print of a navy and yellow oval crossed by coloured stripes">
    <div class="abs card-caption"><div class="card-title">Marlow 2</div><div class="card-date">Lorem ipsum, 22 Feb 2017</div></div>
  </div>
  <div class="abs card card-b" role="img" aria-label="Wave pattern painting in orange, lilac and ochre">
    <div class="abs card-caption"><div class="card-title">Penrose</div><div class="card-date">Lorem ipsum, 22 Feb 2017</div></div>
  </div>
  <svg class="abs arrow" style="left:716px" width="20" height="40" viewBox="0 0 20 40"><path d="M2 2l15 18L2 38" fill="none" stroke="#999" stroke-width="2"/></svg>
</section>

<section class="abs about">
  <h2 class="section-head"><span class="head-mark"></span>About Harwick Moss Fine Art</h2>
  <p class="about-text">Lorem ipsum dolor sit amet, consectetuer adipiscing elit, sed diam nonummy nibh euismod tincidunt ut laoreet dolore magna aliquam erat volutpat. Ut wisi enim ad minim veniam, quis nostrud exerci tation ullamcorper suscipit lobortis nisl ut aliquip ex ea commodo consequat. Duis autem vel eum iriure dolor in hendrerit in vulputate velit esse molestie consequat, vel illum dolore eu feugiat nulla facilisis at vero eros et accumsan et iusto odio dignissim qui blandit praesent luptatum zzril delenit augue duis dolore te feugait nulla facilisi.</p>
</section>

<section class="abs tweets">
  <h2 class="section-head"><span class="head-mark"></span>Social Feeds<span class="see-all">See All Feeds &raquo;</span></h2>
  <div class="tweet"><span class="tweet-badge"></span><p><b>Lorem Ipsum</b> is simply dummy text&nbsp; Tempor - Post post - Ipsum isyt<br>http://demo.site/hm4821<br><b>12 minutes ago</b></p></div>
  <div class="tweet"><span class="tweet-badge"></span><p><b>Lorem Ipsum</b> is simply dummy text&nbsp; Tempor - Post post - Ipsum isyt<br>http://demo.site/hm4821<br><b>12 minutes ago</b></p></div>
</section>

<section class="abs newsletter">
  <div class="abs news-icon">
    <svg width="34" height="34" viewBox="0 0 34 34"><rect x="10" y="12" width="14" height="10" rx="1" fill="none" stroke="#fff" stroke-width="1.5"/><path d="M10 13l7 5 7-5" fill="none" stroke="#fff" stroke-width="1.5"/></svg>
  </div>
  <div class="abs news-title">Join our Newsletter</div>
  <div class="abs news-sub">Stay up to date with the latest news.</div>
  <div class="abs news-input">Email</div>
  <div class="abs news-button">Subscribe</div>
</section>

<footer class="abs site-footer">
  <svg class="abs" style="left:0;top:0" width="750" height="28" viewBox="0 0 750 28"><path d="M0 0h750L375 26z" fill="var(--mist)"/></svg>
  <span class="abs social" style="left:326px" aria-label="Social link one"></span>
  <span class="abs social" style="left:352px" aria-label="Social link two"></span>
  <span class="abs social" style="left:378px" aria-label="Social link three"></span>
  <span class="abs social" style="left:404px" aria-label="Social link four"></span>
  <nav class="abs footer-nav">
    <span class="footer-link">New Releases</span>
    <span class="footer-link">About Us</span>
    <span class="footer-link">Artists</span>
    <span class="footer-link">Location</span>
  </nav>
  <div class="abs copyright">Copyrights © 2017 Harwick Moss Fine Art. All Rights Reserve.</div>
</footer>
<div class="abs stripe"><i style="background:var(--orange)"></i><i style="background:var(--violet)"></i><i style="background:var(--green)"></i><i style="background:var(--orchid)"></i></div>

</body>
</html>
```